Distribution/Printing company needs a web site to inform prospective customers on what we do.

Distribution/Printing/Packaging company needs a web site to inform prospective customers on what we do. Please look at our direct to consumer web site (under development) for an idea of the product lines we sell: storedev.maplewickhaven.com
Logo files are attached as is a flyer that is under development which contains other information about the company (this is to be used for content- not to be posted as is). The web site should be focused on our business customer base and is not intended to be direct to consumer. Site should have a link to our consumer web site.
Site design should be mobile friendly, or mobile could be redirected to a mobile version. This web site will be strictly informational and will not be designed for any sales transactions.

Target Market(s)

Manufacturing and retail businesses, any other multi-site business that would benefit from centralized pricing and budget controls we can provide (banks, medical/dental offices, educational facilities, etc).

Industry/Entity Type

It Company

Coding

Coded - Design and coding required

Number of Pages Required

5+ page

Requirements
Must have
• 1) Top level menu: Products, about us, locations, contact us, news
• 2) page with news/promotions that is easily updated
• 3) "contact us" form (name, company, phone, email address) email link
• 4) link to www.store.maplewickhaven.com with information that lower pricing is available for businesses
• 5) SEO keywords
• 6) Link to powerpoint presentation file
Nice to have
• 1) our phone number should appear on every page near the top

```html
<!DOCTYPE html>
<html lang="en">
<head>
<meta charset="utf-8">
<title>Maplewick Haven Supply — Packaging, Printing, Distribution</title>
<link href="https://fonts.googleapis.com/css2?family=Open+Sans:wght@400;600;700&display=swap" rel="stylesheet">
<style>
:root{
  --ink:#111;
  --header:#141414;
  --footer:#161616;
  --text:#555;
  --muted:#9a9a9a;
  --link:#1f5fa8;
  --accent:#2e8bd8;
  --border:#dedede;
  --band:#f2f2f2;
  --white:#fff;
}
*{margin:0;padding:0;box-sizing:border-box}
html,body{width:858px;height:1200px;overflow:hidden}
body{font-family:"Open Sans",Arial,sans-serif;color:var(--ink);background:var(--white);position:relative}
.abs{position:absolute}
.site-header{position:absolute;left:0;top:0;width:858px;height:84px;background:var(--header)}
.brand{position:absolute;left:70px;top:20px;width:130px;text-align:center;color:var(--white)}
.brand-mark{display:block;margin:0 auto 5px;width:14px;height:14px;border-radius:50%;background:var(--white)}
.brand-name{font-size:10px;font-weight:700;letter-spacing:.2px;text-transform:uppercase;white-space:nowrap}
.brand-tag{font-size:6.5px;font-weight:600;margin-top:2px;white-space:nowrap}
.phone{position:absolute;right:72px;top:17px;color:var(--white);font-size:8.5px;display:flex;align-items:center;gap:5px}
.phone b{font-size:12.5px;font-weight:400}
.main-nav{position:absolute;top:60px;left:0;width:858px;font-size:9.5px;color:var(--white)}
.main-nav a{position:absolute;color:var(--white);text-decoration:none;white-space:nowrap}
.main-nav a.active:after{content:"";position:absolute;left:3px;right:3px;top:15px;height:2px;background:var(--accent)}
.hero{position:absolute;left:0;top:84px;width:858px;height:326px;
  background:linear-gradient(100deg,#c9a22a 0%,#a58a3a 22%,#6b6f78 38%,#2d5aa8 50%,#b08a5e 62%,#c49a68 78%,#6a7a88 100%)}
.hero-title{position:absolute;background:rgba(17,17,17,.92);color:var(--white);text-align:center;text-transform:uppercase;font-weight:400}
.t1{left:273px;top:120px;width:312px;height:46px;font-size:25px;line-height:46px}
.t2{left:306px;top:172px;width:243px;height:37px;font-size:20px;line-height:37px}
.hero-shadow{position:absolute;left:40px;top:410px;width:778px;height:22px;background:radial-gradient(ellipse at top,rgba(0,0,0,.16),rgba(0,0,0,0) 70%)}
.service{position:absolute;top:440px;width:226px;height:192px;border:1px solid var(--border);background:var(--white)}
.service .photo{position:absolute;left:7px;top:7px;width:211px;height:107px}
.service h3{position:absolute;left:10px;top:126px;font-size:14px;font-weight:600;text-transform:uppercase}
.service p{position:absolute;left:10px;top:150px;width:210px;font-size:8.8px;line-height:15px;color:var(--text)}
.products{position:absolute;left:0;top:664px;width:858px;height:246px;background:var(--band);border-top:1px solid #e6e6e6;border-bottom:1px solid #e6e6e6}
.section-title{font-size:14px;font-weight:600;text-transform:uppercase}
.products .section-title{position:absolute;top:24px;width:858px;text-align:center}
.product{position:absolute;top:54px;width:125px;height:156px;background:var(--white);border:1px solid var(--border);text-align:center}
.product .photo{margin:12px auto 0;width:100px;height:84px;border-radius:6px}
.product h4{font-size:12.5px;font-weight:400;color:#333;margin-top:20px}
.product p{font-size:8.8px;color:var(--muted);margin-top:4px}
.product:after{content:"";position:absolute;left:5px;right:5px;bottom:-14px;height:12px;background:radial-gradient(ellipse at top,rgba(0,0,0,.18),rgba(0,0,0,0) 70%)}
.welcome{position:absolute;left:70px;top:936px;width:430px}
.lead{margin-top:22px;font-size:8.8px;line-height:15px;color:var(--link)}
.body-copy{margin-top:14px;font-size:8.8px;line-height:15px;color:var(--text)}
.btn{display:inline-block;margin-top:17px;background:var(--ink);color:var(--white);font-size:8px;padding:8px 9px;text-transform:uppercase;letter-spacing:.3px;text-decoration:none}
.news{position:absolute;left:549px;top:936px;width:240px}
.news-item{margin-top:22px}
.news-item+.news-item{margin-top:16px}
.news-item a{font-size:9.5px;color:var(--link);text-decoration:none}
.news-item p{font-size:8.8px;line-height:15px;color:var(--text);margin-top:3px}
.news-item time{display:block;font-size:8.5px;color:var(--muted);margin-top:2px}
.site-footer{position:absolute;left:0;top:1138px;width:858px;height:62px;background:var(--footer);color:var(--white)}
.copyright{position:absolute;left:72px;top:24px;font-size:9px}
.social{position:absolute;left:660px;top:17px;display:flex;gap:9px}
.social a{width:27px;height:27px;border:2px solid var(--white);border-radius:50%;display:block}
</style>
</head>
<body>
<header class="site-header">
  <div class="brand">
    <span class="brand-mark"></span>
    <div class="brand-name">Maplewick Haven Supply</div>
    <div class="brand-tag">Packaging • Printing • Distribution</div>
  </div>
  <div class="phone">
    <svg width="8" height="13" viewBox="0 0 8 13"><rect x="0.7" y="0.7" width="6.6" height="11.6" rx="1.2" fill="none" stroke="#fff" stroke-width="1.2"/><circle cx="4" cy="10.4" r=".8" fill="#fff"/></svg>
    <span>CALL US:<b>555-010-0147</b></span>
  </div>
  <nav class="main-nav">
    <a class="active" href="#" style="left:325px">HOME</a>
    <a href="#" style="left:397px">ABOUT US</a>
    <a href="#" style="left:487px">SERVICES</a>
    <a href="#" style="left:572px">PRODUCTS</a>
    <a href="#" style="left:662px">NEWS</a>
    <a href="#" style="left:730px">CONTACT US</a>
  </nav>
</header>

<section class="hero" role="img" aria-label="Courier carrying a strapped cardboard box in front of a yellow delivery van">
  <div class="hero-title t1">Meeting all of your</div>
  <div class="hero-title t2">Packaging needs</div>
  <svg class="abs" style="left:21px;top:133px" width="28" height="60" viewBox="0 0 28 60"><polyline points="26,1 2,30 26,59" fill="none" stroke="#fff" stroke-width="1.6"/></svg>
  <svg class="abs" style="left:816px;top:133px" width="28" height="60" viewBox="0 0 28 60"><polyline points="2,1 26,30 2,59" fill="none" stroke="#fff" stroke-width="1.6"/></svg>
</section>
<div class="hero-shadow"></div>

<article class="service" style="left:70px">
  <div class="photo" role="img" aria-label="Warehouse worker packing cardboard boxes" style="background:linear-gradient(120deg,#3b6fb0,#8a6a4c 55%,#c9a275)"></div>
  <h3>Distribution</h3>
  <p>Lorem Ipsum is simply dummy text of the printing and typesetting industryorem.</p>
</article>
<article class="service" style="left:317px">
  <div class="photo" role="img" aria-label="Gloved hands with an ink roller on a colour print sheet" style="background:linear-gradient(180deg,#d8dce2,#8d9096 50%,#d6c84a 75%,#4aa0c8)"></div>
  <h3>Printing</h3>
  <p>Lorem Ipsum is simply dummy text of the printing and typesetting industryorem.</p>
</article>
<article class="service" style="left:562px">
  <div class="photo" role="img" aria-label="Hands lifting a cardboard box from a warehouse shelf" style="background:linear-gradient(120deg,#3d4a3f,#9a7450 50%,#c9a27a)"></div>
  <h3>Packaging</h3>
  <p>Lorem Ipsum is simply dummy text of the printing and typesetting industryorem.</p>
</article>

<section class="products">
  <h2 class="section-title">Our Products</h2>
  <div class="product" style="left:72px"><div class="photo" role="img" aria-label="Stack of cardboard shipping boxes" style="background:radial-gradient(circle,#c99a55,#f4ead9 80%)"></div><h4>Product Name</h4><p>Lorem Ipsum is simply</p></div>
  <div class="product" style="left:222px"><div class="photo" role="img" aria-label="Coloured plastic storage bins" style="background:radial-gradient(circle,#d0b030,#c83a2e 45%,#3a5fb0 65%,#fff 90%)"></div><h4>Product Name</h4><p>Lorem Ipsum is simply</p></div>
  <div class="product" style="left:367px"><div class="photo" role="img" aria-label="Assorted light bulbs" style="background:radial-gradient(circle,#cfd3d8,#f4f5f6 80%)"></div><h4>Product Name</h4><p>Lorem Ipsum is simply</p></div>
  <div class="product" style="left:511px"><div class="photo" role="img" aria-label="Calculator, stapler and office supplies" style="background:radial-gradient(circle,#4a4a4a,#b45a5a 50%,#f3f3f3 85%)"></div><h4>Product Name</h4><p>Lorem Ipsum is simply</p></div>
  <div class="product" style="left:662px"><div class="photo" role="img" aria-label="Cleaning and janitorial supplies" style="background:radial-gradient(circle,#5a78b8,#d0473a 50%,#f3f3f3 85%)"></div><h4>Product Name</h4><p>Lorem Ipsum is simply</p></div>
</section>

<section class="welcome">
  <h2 class="section-title">Welcome to our site!!</h2>
  <p class="lead">Lorem Ipsum is simply dummy text of the printing and typesetting industry. Lorem Ipsum has been the industry's standard dummy text ever since the 1500s, when an unknown printer.</p>
  <p class="body-copy">Aook a galley of type and scrambled it to make a type specimen boolt has survived not only five centuries, but also the leap into electronic typesetting, remaining essentially unchanindustry's standard dummy text ever since the 1500s, when an unknown printeok a galley of type and scrambled it to make a type speci-men boolt has survived not only five centuries, but also the leap into electronic typesetti.</p>
  <a class="btn" href="#">Read more</a>
</section>

<aside class="news">
  <h2 class="section-title">News</h2>
  <div class="news-item"><a href="#">Lorem Ipsum is simply dummy text</a><p>typesetting industry. Lorem Ipsum has been the industry's standard dummy text ever since the 1500.</p><time>April 10-2015</time></div>
  <div class="news-item"><a href="#">Lorem Ipsum is simply dummy text</a><p>typesetting industry. Lorem Ipsum has been the industry's standard dummy text ever since the 1500.</p><time>April 10-2015</time></div>
</aside>

<footer class="site-footer">
  <div class="copyright">© Copyright&nbsp; Maplewick Haven Supply all rights are reserved</div>
  <div class="social">
    <a href="#" aria-label="Social profile 1"></a>
    <a href="#" aria-label="Social profile 2"></a>
    <a href="#" aria-label="Social profile 3"></a>
    <a href="#" aria-label="Social profile 4"></a>
  </div>
</footer>
</body>
</html>
```